Consulting Practice for Charities Needs A Brochure Deisgn

Hi! We need a tri-fold brochure for a Washington, DC based consulting practice that works with charities (NGOs, Associations, etc.) and wealthy donors (philanthropists). Our company, Morrow Civic Advisors, helps nonprofits to implement practices that maximize organizational efficiency and effectiveness - by working directly with board members and staff.
Our clients are well educated and quite sophisticated (some charities are international with multi-million dollar budgets, while others are quite local and small) This brochure will be handed to them by some of our 'referral partners' (law firms, accountants and even governmental agencies) in addition to being given out during our presentations. We draw inspiration from nature and would like to somehow include a "natural / eco-friendly" feel to the piece, including natural colors .... that being said, not in any way "folksy" - it must be sophisticated.

Target Market(s)

nonprofit executive directors, board chairs, wealth holders (philanthropists)

Industry/Entity Type

Consulting

Requirements
Must have
• I uploaded a word file with content (text) - most of that needs to be on the brochure ... but ... if it looks too crowded, let me know and I'll reduce
Nice to have
• pop-out quotes (maybe from testimonials??), nature - theme of some kind but also photo of boardroom (links to samples are like are uploaded in a word doc below)
Should not have
• nothing cute ... nothing too feminine

```html
<!DOCTYPE html>
<html lang="en">
<head>
<meta charset="utf-8">
<title>Morrow Civic Advisors – Trifold Brochure</title>
<link rel="stylesheet" href="https://fonts.googleapis.com/css2?family=Roboto+Slab:wght@300;400;700&display=swap">
<style>
:root{
  --board:#939598;
  --purple:#7a6eb2;
  --purple-dark:#665a9f;
  --lavender:#e9e6f3;
  --orange:#f7941d;
  --ink:#3b3b3f;
  --white:#ffffff;
}
*{box-sizing:border-box;margin:0;padding:0}
html,body{width:1200px;height:970px;overflow:hidden;background:var(--board)}
body{position:relative;font-family:"Roboto Slab",serif;color:var(--ink)}
.sheet{position:absolute;overflow:hidden;background:var(--white)}
.panel{position:absolute;top:0;width:192px;height:447px;overflow:hidden}
svg.swoosh{position:absolute;left:0;width:100%;display:block}

.title-block{position:absolute;left:760px;top:120px;width:290px;text-align:center;color:var(--white)}
.title-block .big-mark{font-size:108px;font-weight:300;letter-spacing:2px;line-height:1}
.title-block h1{font-size:27px;font-weight:700;margin-top:60px;line-height:1.75;letter-spacing:.5px}

.brand{text-align:center}
.brand .mark{display:block;font-weight:400;font-size:40px;line-height:1;color:var(--purple)}
.brand .band{display:inline-block;margin-top:4px;background:var(--purple);color:var(--white);font-size:7.4px;padding:2px 4px;letter-spacing:.2px}

.photo{position:absolute;left:0;width:100%}
.photo-lake{background:linear-gradient(180deg,#dfe3e6 0%,#cfd6d8 30%,#6d8a4e 52%,#3f5e2f 66%,#5f7f46 78%,#495d3b 100%)}

.cover .photo{top:0;height:310px}
.cover .brand{position:absolute;top:34px;left:0;width:100%}
.cover-copy{position:absolute;top:352px;left:10px;right:10px;text-align:center}
.cover-copy h2{color:var(--orange);font-size:11.2px;font-weight:700;line-height:1.3}
.cover-copy p{font-size:6.4px;line-height:1.35;margin-top:7px}
.cover-copy .url{color:var(--orange);font-size:7px;margin-top:10px;display:block}

.back{background:var(--purple)}
.back .brand .mark{color:var(--white);margin-top:68px;font-size:36px}
.contacts{position:absolute;top:116px;width:100%;text-align:center;color:var(--white)}
.contact{margin-bottom:9px}
.contact .ic{display:block;width:14px;height:14px;margin:0 auto 3px}
.contact .phone{display:block;font-size:10.5px;line-height:1.2;letter-spacing:.3px}
.contact .small{display:block;font-size:7px;line-height:1.3}
.back .lower{position:absolute;left:0;top:300px;width:100%;height:147px;background:var(--white)}
.certs{position:absolute;top:335px;width:100%;text-align:center}
.certs h3{color:var(--orange);font-size:11px;font-weight:700;letter-spacing:.3px}
.badge-row{display:flex;justify-content:center;gap:12px;margin-top:10px}
.badge{display:block;background:#d8d8de;border-radius:3px}
.badge.wide{width:118px;height:20px}
.badge.tri{width:30px;height:36px;background:#c9cbd6}
.badge.seal{width:50px;height:36px;background:#dfe4d9}

.testimonials{background:linear-gradient(180deg,#f1eff8 0%,#e3dfef 70%,#d9d4ea 100%);padding:13px 12px 0 15px}
.testimonials header{display:flex;align-items:center;gap:8px;margin-bottom:10px}
.quote-ic{width:26px;height:26px;border:1.5px solid var(--purple);border-radius:50%;color:var(--purple);font-size:18px;font-weight:700;text-align:center;line-height:28px;background:var(--white)}
.testimonials h3{color:var(--orange);font-size:10px;font-weight:700}
.quote{margin-bottom:9px;font-size:6.6px;line-height:1.32}
.quote cite{display:block;font-style:normal;color:var(--purple);font-weight:700;margin-bottom:1px}

.spread-photos{position:absolute;top:0;left:0;width:576px;height:118px;display:flex}
.spread-photos .ph{height:100%}
.ph-meeting{width:190px;background:linear-gradient(160deg,#e9edf1 0%,#c7cdd4 45%,#8b8f98 75%,#5a5d66 100%)}
.ph-lake{width:193px;background:linear-gradient(180deg,#6f9fd6 0%,#b9d2ea 38%,#3f5b32 58%,#2d4430 72%,#5d7ea6 100%)}
.ph-reeds{width:193px;background:linear-gradient(180deg,#8a80bd 0%,#9c93c8 45%,#7d72b4 100%);position:relative}
.ph-reeds .overlay{position:absolute;top:38px;left:0;width:100%;text-align:center;color:var(--white);font-size:12.5px;line-height:1.28;text-shadow:0 1px 3px rgba(40,30,80,.8)}
.ph-reeds .overlay strong{font-weight:700}
.rule{position:absolute;top:118px;left:0;width:576px;height:3px;background:var(--purple)}
.col{position:absolute;top:136px;width:192px;padding:0 14px}
.col h3{display:flex;align-items:center;gap:7px;color:var(--orange);font-size:10.5px;font-weight:700;margin-bottom:9px}
.col h3 svg{width:20px;height:18px}
.col p{font-size:6px;line-height:1.3;margin-bottom:7px}
.col h4{color:var(--orange);font-size:6.8px;font-weight:400;margin-bottom:1px}
.col .lead{color:var(--purple);font-size:6.8px;margin-bottom:5px}
.chevrons{display:flex;margin:4px 0 10px}
.chev{position:relative;height:20px;width:56px;color:var(--white);font-size:6.4px;line-height:1.1;padding:3px 0 0 9px;clip-path:polygon(0 0,88% 0,100% 50%,88% 100%,0 100%,10% 50%)}
.chev:first-child{clip-path:polygon(0 0,88% 0,100% 50%,88% 100%,0 100%);padding-left:6px}
.chev.o{background:var(--orange)}
.chev.g{background:#9a9aa2}
.bullets{list-style:none;font-size:6px;line-height:1.3}
.bullets li{position:relative;padding-left:9px;margin-bottom:6px}
.bullets li::before{content:"";position:absolute;left:1px;top:3px;width:3px;height:3px;border-radius:50%;background:var(--purple)}
.ph-crowd{height:68px;margin:6px 0 10px;background:linear-gradient(180deg,#f4f4f6 0%,#b9bcc4 45%,#7c808a 100%)}
.services-head .mini-mark{margin-left:auto;color:var(--purple);font-weight:400;font-size:17px}
.services{list-style:none;font-size:6.5px;line-height:1.25}
.services li{position:relative;padding-left:10px;margin-bottom:5.2px}
.services li::before{content:"";position:absolute;left:1px;top:2.5px;width:3px;height:3px;border-radius:50%;background:var(--purple)}
.services ul{list-style:none;margin-top:5px;padding-left:14px}
.services ul li::before{background:var(--orange);width:2.5px;height:2.5px}
.spread-url{position:absolute;left:0;bottom:6px;width:576px;text-align:center;font-size:7px;color:var(--ink)}
</style>
</head>
<body>

<section class="sheet outside" style="left:39px;top:31px;width:577px;height:447px">

  <article class="panel testimonials" style="left:0">
    <header><div class="quote-ic">“</div><h3>TESTIMONIAL</h3></header>
    <div class="quote"><cite>Helen Ashby (CEO, Community Homes Partners)</cite>“I would recommend Claire without reservation. Her governance training and her knowledge of both Board dynamics and the needs of donors is uniquely helpful.”</div>
    <div class="quote"><cite>Daniel Reyes, CTFA (Client, Philanthropist)</cite>“I've had the honor and distinct privilege of working with Claire through her Board Coaching &amp; Training program. The board self-assessment process is thorough, insightful and necessary, if like me, you are challenged with finding the right organization to align with. Leveraging her expertise, guidance and deep connections throughout the Non-Profit space, Claire carefully screened several organizations as potential candidates, and went so far as to arrange introductory meetings with a select few. The entire process was educational, and an exceptional”</div>
    <div class="quote"><cite>Margaret Olsen (Past Chairman, National Arts Health Society)</cite>“I wish you could have heard the board's comments. They were unanimously and warmly enthusiastic, saying it was the best thing we, as a board, have ever done... Thank you for the thought and combination of emotional and intellectual intelligence that you brought to the presentation.”</div>
    <div class="quote"><cite>Robert Lane (Client, Journalist and Broadcaster)</cite>“Claire is at forefront of the new era of responsible philanthropy ... Most importantly, she has the rare ability to take a vision and turn it into a coherent plan of action.”</div>
    <svg class="swoosh" style="bottom:0;height:40px" viewBox="0 0 192 40" preserveAspectRatio="none" aria-hidden="true">
      <path d="M0 40 L0 30 C60 28 120 18 192 0 C140 22 80 34 0 40Z" fill="var(--purple)"/>
      <path d="M0 30 C60 26 120 16 150 6" stroke="var(--orange)" stroke-width="1" fill="none"/>
    </svg>
  </article>

  <article class="panel back" style="left:192px">
    <div class="brand"><span class="mark">MCA</span></div>
    <div class="contacts">
      <div class="contact">
        <svg class="ic" viewBox="0 0 14 14" aria-hidden="true"><circle cx="7" cy="7" r="6.2" fill="none" stroke="#fff" stroke-width="1.2"/><path d="M5 4 L6.4 5.6 L5.8 6.4 C6.3 7.4 6.8 7.9 7.7 8.3 L8.5 7.7 L10 9.1 L9.2 10.1 C7 10 4.2 7.2 4.1 5Z" fill="#fff"/></svg>
        <span class="phone">+1.202.555.0148</span>
      </div>
      <div class="contact">
        <svg class="ic" viewBox="0 0 14 14" aria-hidden="true"><circle cx="7" cy="7" r="6.2" fill="none" stroke="#fff" stroke-width="1.2"/><rect x="4" y="5" width="6" height="4.2" fill="#fff"/><path d="M4 5 L7 7.3 L10 5" stroke="var(--purple)" stroke-width=".7" fill="none"/></svg>
        <span class="small">info@MorrowCivicAdvisors.com<br>MorrowCivicAdvisors.com</span>
      </div>
      <div class="contact">
        <svg class="ic" viewBox="0 0 14 14" aria-hidden="true"><circle cx="7" cy="7" r="6.2" fill="none" stroke="#fff" stroke-width="1.2"/></svg>
        <span class="small">in/morrowcivicadvisors</span>
      </div>
    </div>
    <svg class="swoosh" style="top:212px;height:92px" viewBox="0 0 192 92" preserveAspectRatio="none" aria-hidden="true">
      <path d="M0 40 C40 80 120 86 192 58 L192 92 L0 92Z" fill="#8a7fc0"/>
      <path d="M0 22 C30 60 110 80 192 66" stroke="var(--orange)" stroke-width="1" fill="none"/>
      <path d="M0 70 C60 92 140 80 192 72 L192 92 L0 92Z" fill="#fff"/>
    </svg>
    <div class="lower"></div>
    <div class="certs">
      <h3>CERTIFICATES:</h3>
      <div class="badge-row"><span class="badge wide"></span></div>
      <div class="badge-row"><span class="badge tri"></span><span class="badge seal"></span></div>
    </div>
  </article>

  <article class="panel cover" style="left:385px">
    <div class="photo photo-lake" role="img" aria-label="Forest lake with pine trees and marsh grass under a pale sky"></div>
    <div class="brand"><span class="mark">MCA</span><span class="band">MORROW CIVIC ADVISORS</span></div>
    <svg class="swoosh" style="top:292px;height:40px" viewBox="0 0 192 40" preserveAspectRatio="none" aria-hidden="true">
      <path d="M0 20 C60 -2 130 -4 192 8 L192 40 L0 40Z" fill="var(--purple)"/>
      <path d="M0 30 C60 16 130 14 192 20 L192 40 L0 40Z" fill="#fff"/>
      <path d="M0 30 C60 16 130 14 192 20" stroke="var(--orange)" stroke-width="1" fill="none"/>
    </svg>
    <div class="cover-copy">
      <h2>CHANGING THE CULTURE<br>OF PHILANTHROPY</h2>
      <p>We help nonprofit clients excel by implementing exceptional governance practices.<br>We counsel private clients on involvement with sound philanthropic enterprises.</p>
      <span class="url">MorrowCivicAdvisors.com</span>
    </div>
  </article>
</section>

<div class="title-block">
  <div class="big-mark">MCA</div>
  <h1>TRIFOLD<br>BROCHURE DESIGN</h1>
</div>

<section class="sheet" style="left:112px;top:497px;width:193px;height:447px">
  <article class="panel cover" style="left:0;width:193px">
    <div class="photo photo-lake" role="img" aria-label="Forest lake with pine trees and marsh grass under a pale sky"></div>
    <div class="brand"><span class="mark">MCA</span><span class="band">MORROW CIVIC ADVISORS</span></div>
    <svg class="swoosh" style="top:292px;height:40px" viewBox="0 0 192 40" preserveAspectRatio="none" aria-hidden="true">
      <path d="M0 20 C60 -2 130 -4 192 8 L192 40 L0 40Z" fill="var(--purple)"/>
      <path d="M0 30 C60 16 130 14 192 20 L192 40 L0 40Z" fill="#fff"/>
      <path d="M0 30 C60 16 130 14 192 20" stroke="var(--orange)" stroke-width="1" fill="none"/>
    </svg>
    <div class="cover-copy">
      <h2>CHANGING THE CULTURE<br>OF PHILANTHROPY</h2>
      <p>We help nonprofit clients excel by implementing exceptional governance practices.<br>We counsel private clients on involvement with sound philanthropic enterprises.</p>
      <span class="url">MorrowCivicAdvisors.com</span>
    </div>
  </article>
</section>

<section class="sheet" style="left:320px;top:497px;width:192px;height:447px">
  <article class="panel back" style="left:0">
    <div class="brand"><span class="mark">MCA</span></div>
    <div class="contacts">
      <div class="contact">
        <svg class="ic" viewBox="0 0 14 14" aria-hidden="true"><circle cx="7" cy="7" r="6.2" fill="none" stroke="#fff" stroke-width="1.2"/><path d="M5 4 L6.4 5.6 L5.8 6.4 C6.3 7.4 6.8 7.9 7.7 8.3 L8.5 7.7 L10 9.1 L9.2 10.1 C7 10 4.2 7.2 4.1 5Z" fill="#fff"/></svg>
        <span class="phone">+1.202.555.0148</span>
      </div>
      <div class="contact">
        <svg class="ic" viewBox="0 0 14 14" aria-hidden="true"><circle cx="7" cy="7" r="6.2" fill="none" stroke="#fff" stroke-width="1.2"/><rect x="4" y="5" width="6" height="4.2" fill="#fff"/><path d="M4 5 L7 7.3 L10 5" stroke="var(--purple)" stroke-width=".7" fill="none"/></svg>
        <span class="small">info@MorrowCivicAdvisors.com<br>MorrowCivicAdvisors.com</span>
      </div>
      <div class="contact">
        <svg class="ic" viewBox="0 0 14 14" aria-hidden="true"><circle cx="7" cy="7" r="6.2" fill="none" stroke="#fff" stroke-width="1.2"/></svg>
        <span class="small">in/morrowcivicadvisors</span>
      </div>
    </div>
    <svg class="swoosh" style="top:212px;height:92px" viewBox="0 0 192 92" preserveAspectRatio="none" aria-hidden="true">
      <path d="M0 40 C40 80 120 86 192 58 L192 92 L0 92Z" fill="#8a7fc0"/>
      <path d="M0 22 C30 60 110 80 192 66" stroke="var(--orange)" stroke-width="1" fill="none"/>
      <path d="M0 70 C60 92 140 80 192 72 L192 92 L0 92Z" fill="#fff"/>
    </svg>
    <div class="lower"></div>
    <div class="certs">
      <h3>CERTIFICATES:</h3>
      <div class="badge-row"><span class="badge wide"></span></div>
      <div class="badge-row"><span class="badge tri"></span><span class="badge seal"></span></div>
    </div>
  </article>
</section>

<section class="sheet inside" style="left:580px;top:496px;width:576px;height:447px;background:linear-gradient(180deg,#fff 70%,#ebe8f4 100%)">
  <div class="spread-photos">
    <div class="ph ph-meeting" role="img" aria-label="Business team meeting around a boardroom table"></div>
    <div class="ph ph-lake" role="img" aria-label="Calm lake framed by evergreen forest under a blue sky"></div>
    <div class="ph ph-reeds" role="img" aria-label="Lake reeds tinted in purple">
      <div class="overlay">Guiding Responsible<br>Philanthropy<br><strong>Improving Board<br>Governance</strong></div>
    </div>
  </div>
  <div class="rule"></div>

  <div class="col" style="left:0">
    <h3><svg viewBox="0 0 20 18" aria-hidden="true"><circle cx="6" cy="4" r="3" fill="var(--purple)"/><rect x="2" y="8" width="8" height="9" rx="2" fill="var(--purple)"/><circle cx="14" cy="6" r="2.5" fill="var(--purple)"/><rect x="11" y="10" width="7" height="7" rx="2" fill="var(--purple)"/></svg>WHO WE ARE:</h3>
    <p>Founded in 2010 by Claire Elise Morrow, MCA was inspired by the national climate for stronger governance and deeper board engagement. Since then, we've worked with hundreds of board members to improve the impact of their philanthropic efforts.</p>
    <p>Our energetic and patient team of experts in nonprofit governance, operations and management will provide a comprehensive approach to problem solving, training and coaching. The result?</p>
    <div class="chevrons">
      <div class="chev o">Better<br>Boards</div>
      <div class="chev g" style="width:72px">Stronger<br>Organizations</div>
      <div class="chev o">Greater<br>Impact</div>
    </div>
    <div class="lead">MCA consultants will:</div>
    <ul class="bullets">
      <li>Bring new perspectives and skills for strategic or generative (big picture) thinking</li>
      <li>Challenge your assumptions</li>
      <li>Offer innovative approaches to problem solving</li>
      <li>Identify sources of dysfunction</li>
      <li>Devise tactics to improve decision making or communication</li>
      <li>Make breakthrough improvements</li>
    </ul>
  </div>

  <div class="col" style="left:192px">
    <h3><svg viewBox="0 0 20 18" aria-hidden="true"><circle cx="4" cy="4" r="2.3" fill="var(--purple)"/><circle cx="10" cy="4" r="2.3" fill="var(--purple)"/><circle cx="16" cy="4" r="2.3" fill="var(--purple)"/><rect x="1.5" y="7.5" width="5" height="9" rx="1.5" fill="var(--purple)"/><rect x="7.5" y="7.5" width="5" height="9" rx="1.5" fill="var(--purple)"/><rect x="13.5" y="7.5" width="5" height="9" rx="1.5" fill="var(--purple)"/></svg>WHAT WE DO:</h3>
    <h4>Organizational Clients</h4>
    <p>20th century developmental psychologist Henrik Dahl asserted that for individuals, conflict and crisis are positive and necessary; they are "sources of growth, strength, and commitment." We believe the same can be true of organizations. MCA helps nonprofits manage change and emerge triumphantly. Through coaching, we help organizations implement practices to maximize efficiency and effectiveness - whether preparing for transition, coping with chaos, or simply pursuing continued high performance - by working directly with board members and staff. Our methods are informed by research and honed by over 20 years of practice.</p>
    <div class="ph-crowd" role="img" aria-label="Large group of business people standing together"></div>
    <h4>Private Clients</h4>
    <p>MCA philanthropic counsel helps individuals adopt impactful practices in their charitable endeavors.</p>
  </div>

  <div class="col" style="left:384px">
    <h3 class="services-head"><svg viewBox="0 0 20 18" aria-hidden="true"><circle cx="5" cy="3.5" r="2.5" fill="var(--purple)"/><circle cx="15" cy="3.5" r="2.5" fill="var(--purple)"/><rect x="2" y="7" width="6" height="10" rx="1.5" fill="var(--purple)"/><rect x="12" y="7" width="6" height="10" rx="1.5" fill="var(--purple)"/><rect x="7" y="9" width="6" height="2" fill="var(--purple)"/></svg>SERVICES<span class="mini-mark">MCA</span></h3>
    <ul class="services">
      <li>Board and Senior Staff Coaching</li>
      <li>Workshops, Seminars and Retreats including:
        <ul>
          <li>Roles &amp; Responsibilities</li>
          <li>Fundraising</li>
          <li>Succession Planning</li>
          <li>Board Self-Assessments</li>
          <li>Strategic Planning</li>
          <li>Board Recruitment Training</li>
          <li>Communications Development</li>
          <li>Grassroots Advocacy</li>
          <li>Mergers &amp; Acquisitions</li>
        </ul>
      </li>
      <li>Philanthropic Counsel</li>
      <li>Board Placement</li>
      <li>Board Member Recruitment</li>
      <li>Board Retreat Planning &amp; Facilitation</li>
    </ul>
  </div>

  <svg class="swoosh" style="bottom:0;height:46px" viewBox="0 0 576 46" preserveAspectRatio="none" aria-hidden="true">
    <path d="M0 20 C120 40 300 46 576 14 L576 46 L0 46Z" fill="#d9d4ea"/>
    <path d="M0 6 C80 20 160 32 240 44 L0 46Z" fill="var(--purple)"/>
    <path d="M0 14 C100 30 300 40 576 8" stroke="var(--orange)" stroke-width="1" fill="none"/>
    <path d="M360 46 C440 40 520 30 576 18 L576 46Z" fill="var(--purple)"/>
  </svg>
  <div class="spread-url">MorrowCivicAdvisors.com</div>
</section>

</body>
</html>
```